Business card for denture clinic Veltrimora

We need a new business card with our new logo. We are a denture clinic in New Zealand with our target market being 45+ years old. We would need a space on the back to write our patients next appointment on. We would space for only one appointment rather than a list. We will attach a photo showing an example of this. But of course, we would like to see your twist on this. We want it to be bold and easy to read and a good mixture of professional but modern. We have attached our logo to be used on the card.

Target Market(s)

People aged 45+ needing dentures

Industry/Entity Type

Dental

Contact Information for Business Card

We want our logo on the front and the space to write an appointment on the back. I've attached an example our our old business card showing this. We need to have the technicians details on the front.

Font styles to use
Sans Serif

Colors
0255a3
919191
fbfbfb

Requirements
Must have
• The following details:
• Liam Dorsett BDT, PGDipCDentTech Calverin
• Dental Prosthetist
• Phone numbers: 0800 47 3125
• 09 572 1394
• Email: liam@veltrimora.co.nz
• www.veltrimora.co.nz
• Address: 14 Marlow Crest Road
• Halbrook West
• Auckland 0793
Nice to have
• We would like our business cards to have more than just two colours as we want them to be more vibrant. We have uploaded an example of a business card we liked that showed this.

```html
<!DOCTYPE html>
<html lang="en">
<head>
<meta charset="utf-8">
<title>Veltrimora Business Card</title>
<link rel="stylesheet" href="https://fonts.googleapis.com/css2?family=Open+Sans:wght@300;400;600;700&display=swap">
<style>
  :root {
    --brand-blue: #0255a3;
    --brand-grey: #919191;
    --card-white: #fbfbfb;
    --accent-teal: #13968f;
    --text-dark: #4a4a4a;
    --backdrop: #e6e6e6;
  }
  * { box-sizing: border-box; margin: 0; padding: 0; }
  html, body {
    width: 1200px; height: 900px; overflow: hidden;
    background: var(--backdrop);
    font-family: "Open Sans", Arial, sans-serif;
  }
  .sheet {
    width: 1200px; height: 900px;
    display: flex; align-items: center; justify-content: center; gap: 60px;
  }
  .card {
    position: relative;
    width: 525px; height: 300px;
    background: var(--card-white);
    box-shadow: 0 6px 18px rgba(0,0,0,0.12);
    overflow: hidden;
  }
  /* Front */
  .technician { position: absolute; left: 28px; top: 26px; }
  .technician__name {
    color: var(--brand-blue); font-weight: 700; font-size: 21px; letter-spacing: 0.5px;
    text-transform: uppercase;
  }
  .technician__name .post-nominal { font-size: 13px; font-weight: 600; margin-left: 4px; }
  .technician__qual {
    color: var(--brand-blue); font-weight: 600; font-size: 13px; letter-spacing: 0.5px;
    text-transform: uppercase; margin-top: 1px;
  }
  .technician__role { color: var(--text-dark); font-size: 13px; margin-top: 2px; }
  .contact { position: absolute; left: 28px; top: 130px; list-style: none; }
  .contact__item {
    display: flex; align-items: center; gap: 7px;
    color: var(--text-dark); font-size: 13px; line-height: 19px;
  }
  .contact__icon { width: 10px; height: 10px; fill: var(--brand-blue); flex: none; }
  .brand {
    position: absolute; right: 40px; top: 132px;
    display: flex; align-items: center; gap: 10px;
  }
  .brand__square { width: 40px; height: 40px; background: var(--brand-blue); }
  .brand__name {
    color: var(--brand-blue); font-weight: 700; font-size: 32px; letter-spacing: 1px;
    text-transform: uppercase;
  }
  .address-band {
    position: absolute; left: 0; right: 0; bottom: 0; height: 62px;
    background: var(--accent-teal);
    display: flex; align-items: center; padding-left: 28px;
    color: #fff; font-size: 14px; letter-spacing: 0.3px;
  }
  /* Back */
  .appointment { position: absolute; left: 60px; right: 60px; top: 78px; }
  .appointment__title {
    color: var(--accent-teal); font-weight: 400; font-size: 20px; letter-spacing: 1px;
    text-transform: uppercase; text-align: center; margin-bottom: 34px;
  }
  .appointment__row {
    display: flex; align-items: flex-end; gap: 14px; margin-bottom: 26px;
    color: var(--accent-teal); font-size: 15px; letter-spacing: 1px; text-transform: uppercase;
  }
  .appointment__label { width: 50px; }
  .appointment__line { flex: 1; border-bottom: 1.5px solid var(--accent-teal); height: 18px; }
</style>
</head>
<body>
<main class="sheet">
  <section class="card card--front" aria-label="Card front">
    <div class="technician">
      <h1 class="technician__name">Liam Dorsett<span class="post-nominal">BDT,</span></h1>
      <p class="technician__qual">PG Dip Dent Tech Calverin</p>
      <p class="technician__role">Dental Prosthetist</p>
    </div>
    <ul class="contact">
      <li class="contact__item">
        <svg class="contact__icon" viewBox="0 0 10 10" aria-hidden="true"><path d="M2 0.5 L3.6 2.6 L2.7 3.6 Q3.8 5.9 6.2 7.2 L7.3 6.3 L9.5 7.9 L8.4 9.5 Q4.5 9.3 0.5 1.6 Z"/></svg>
        0800 47 3125
      </li>
      <li class="contact__item">
        <svg class="contact__icon" viewBox="0 0 10 10" aria-hidden="true"><path d="M2 0.5 L3.6 2.6 L2.7 3.6 Q3.8 5.9 6.2 7.2 L7.3 6.3 L9.5 7.9 L8.4 9.5 Q4.5 9.3 0.5 1.6 Z"/></svg>
        09 572 1394
      </li>
      <li class="contact__item">
        <svg class="contact__icon" viewBox="0 0 10 10" aria-hidden="true"><path d="M0 2 H10 V8.5 H0 Z M0.8 2.6 L5 5.6 L9.2 2.6" stroke="#fff" stroke-width="0.8"/></svg>
        liam@veltrimora.co.nz
      </li>
    </ul>
    <div class="brand">
      <span class="brand__square" aria-hidden="true"></span>
      <span class="brand__name">Veltrimora</span>
    </div>
    <div class="address-band">14 Marlow Crest Road Halbrook West Auckland 0793</div>
  </section>

  <section class="card card--back" aria-label="Card back">
    <div class="appointment">
      <h2 class="appointment__title">Your Next Appointment</h2>
      <div class="appointment__row"><span class="appointment__label">Date</span><span class="appointment__line"></span></div>
      <div class="appointment__row"><span class="appointment__label">Time</span><span class="appointment__line"></span></div>
    </div>
  </section>
</main>
</body>
</html>
```